Designer sehr zu empfehlen, engagiert und unermüdlich auf Wünsche eingehend. Gerne wieder.
Zielgruppe
Ich berate im Bereich der Telemedizin. Zielgruppe sind Ärzte, Krankenkassen, Politiker.
Aufgabenstellung
Auf der Visitenkarte sollen Adresse, e-mail, Handynummer vorhanden sein.
Briefpapier bitte im Pages-Format.

```html
<!DOCTYPE html>
<html lang="de">
<head>
<meta charset="utf-8">
<title>kuravio Telemedizin – Geschäftsausstattung</title>
<link href="https://fonts.googleapis.com/css2?family=Exo+2:wght@300;400&display=swap" rel="stylesheet">
<style>
:root{
  --stage:#a9aaad;
  --paper:#ffffff;
  --green:#97bf23;
  --grey:#6a6a6c;
  --ink:#767678;
}
*{margin:0;padding:0;box-sizing:border-box}
html,body{width:1029px;height:1200px;overflow:hidden}
body{background:var(--stage);font-family:"Exo 2",sans-serif;font-weight:300;color:var(--ink);position:relative}
.sheet,.card{position:absolute;background:var(--paper);box-shadow:6px 8px 10px rgba(0,0,0,.25)}
.letterhead{left:68px;top:89px;width:720px;height:1019px}
.brand{position:absolute;color:var(--grey);font-weight:400;line-height:1;display:flex;align-items:flex-end;gap:8px}
.brand .dot{border-radius:50%;background:var(--green);flex:none}
.brand .name{display:block}
.brand .tag{display:block;letter-spacing:.22em;margin-top:3px}
.letterhead .brand{left:77px;top:45px}
.letterhead .brand .dot{width:40px;height:40px}
.letterhead .brand .name{font-size:52px}
.letterhead .brand .tag{font-size:16px}
.contact{position:absolute;font-size:9px;line-height:11px;border-left:1px solid var(--green)}
.contact p + p{margin-top:2px}
.letterhead .contact{left:523px;top:0;height:120px;padding:44px 0 0 9px}
.sender{position:absolute;left:85px;top:168px;font-size:7px}
.sender i{color:var(--green);font-style:normal;padding:0 3px}
.fold{position:absolute;left:0;width:17px;border-top:1px solid var(--green)}
.footer-col{position:absolute;top:961px;height:58px;border-left:1px solid var(--green);padding:9px 0 0 8px;font-size:8.5px;line-height:11px}
.card-front{left:642px;top:413px;width:293px;height:186px;background:var(--green)}
.card-front .brand{left:40px;top:62px;color:#fff}
.card-front .brand .dot{width:30px;height:30px;background:#fff}
.card-front .brand .name{font-size:40px}
.card-front .brand .tag{font-size:12px}
.card-back{left:642px;top:642px;width:292px;height:185px;border:1px solid #8c8c8c}
.card-back .brand{left:20px;top:20px}
.card-back .brand .dot{width:20px;height:20px}
.card-back .brand .name{font-size:28px}
.card-back .brand .tag{font-size:9px}
.person{position:absolute;left:23px;top:88px}
.person .who{font-size:12.5px;color:var(--grey);font-weight:400}
.person .role{font-size:8px;margin-top:2px}
.card-back .contact{left:157px;top:87px;height:98px;padding:5px 0 0 8px;font-size:8.5px}
</style>
</head>
<body>
<section class="sheet letterhead">
  <div class="brand"><span class="dot"></span><span><span class="name">kuravio</span><span class="tag">Telemedizin</span></span></div>
  <div class="contact">
    <p>kuravio Telemedizin<br>Lindenweg 8<br>51627 Beispielstadt</p>
    <p>Telefon&nbsp;&nbsp;04321 987650<br>Mobil&nbsp;&nbsp;&nbsp;&nbsp;&nbsp;0172 87654321</p>
    <p>kontakt@kuravio.de<br>www.kuravio.de</p>
  </div>
  <p class="sender">kuravio Telemedizin<i>|</i>Lindenweg 8<i>|</i>51627 Beispielstadt</p>
  <span class="fold" style="top:360px"></span>
  <span class="fold" style="top:509px"></span>
  <div class="footer-col" style="left:249px">Inhaberin: Lena Beispiel<br>UST-IdNr.: DE98765432100</div>
  <div class="footer-col" style="left:409px">Bankverbindung:<br>Beispielbank</div>
  <div class="footer-col" style="left:523px">IBAN: DE 9876 5432 0002 7713 05<br>BIC: XXXXXXXXXXX</div>
</section>

<section class="card card-front">
  <div class="brand"><span class="dot"></span><span><span class="name">kuravio</span><span class="tag">Telemedizin</span></span></div>
</section>

<section class="card card-back">
  <div class="brand"><span class="dot"></span><span><span class="name">kuravio</span><span class="tag">Telemedizin</span></span></div>
  <div class="person"><p class="who">Lena Beispiel</p><p class="role">Berufsbezeichnung</p></div>
  <div class="contact">
    <p>kuravio Telemedizin<br>Lindenweg 8<br>51627 Beispielstadt</p>
    <p>Telefon&nbsp;&nbsp;04321 987650<br>Mobil&nbsp;&nbsp;&nbsp;&nbsp;&nbsp;0172 87654321</p>
    <p>kontakt@kuravio.de<br>www.kuravio.de</p>
  </div>
</section>
</body>
</html>
```